Web Page Graphics

I require graphics work on shopping cart websites- banners, callouts, etc..
It is for a store that sells security cameras. I'd like to approach with a minimalist design; simple, uncluttered..
To start, I need a simple 200 x 266 callout graphic for an online store that tells users technical support is available, provides a phone number and hours. Simple.
Next, I need 3 main banners @ 770 x 328 each, illustrating various products, categories, and text in the form of features (or bullet points)
Lastly, 4 smaller callouts will appear under main banner @ 191 x 75 each. These will each include a vector icon and provide basic info, Ex: lowest prices, free shipping, etc. Text should just be placeholder dummy text.
Updates
Please see attached files.
Please note- project is for 3 banners, callout, and 4 small text boxes (see mockup)
Target Market(s)
Retail - small business and home owners
Industry/Entity Type
Shopping
Requirements
Must have
- Prior work to show

```html
<!DOCTYPE html>
<html lang="en">
<head>
<meta charset="utf-8">
<title>Lensport Security Store</title>
<link rel="stylesheet" href="https://fonts.googleapis.com/css2?family=Open+Sans:wght@400;600;700&family=Roboto+Condensed:ital,wght@0,400;0,700;1,400;1,700&display=swap">
<style>
:root{
  --red:#e8604c;
  --red-dark:#d9492f;
  --text:#444;
  --muted:#777;
  --line:#dcdcdc;
  --panel:#f7f7f7;
  --lime:#b9d532;
  --notice:#fbfae6;
  --notice-line:#efe7a6;
  --navy:#123a8c;
  --yellow:#f6e51c;
}
*{box-sizing:border-box;margin:0;padding:0}
html,body{width:1200px;height:1152px;overflow:hidden;background:#fff;position:relative}
body{font-family:"Open Sans",sans-serif;color:var(--text)}
.viewport{position:absolute;left:0;top:0;width:1200px;height:1152px;overflow:hidden}
.stage{position:absolute;left:0;top:0;width:1044px;height:1009px;overflow:hidden;transform:scale(1.1494,1.1417);transform-origin:0 0}
.abs{position:absolute}

.top-bar{left:0;top:0;width:1044px;height:32px;background:linear-gradient(#f4f4f4,#e3e3e3);border-bottom:1px solid #d4d4d4}
.top-links{right:123px;top:7px;font-size:11.5px;color:#555;display:flex;gap:7px}
.top-links .welcome{color:var(--red)}
.top-links .sep{color:#bbb}

.brand{left:115px;top:60px;display:flex;align-items:center;gap:9px;font-size:22px;font-weight:600;color:var(--red)}
.brand .mark{width:26px;height:26px;background:var(--red)}

.perk{top:61px;display:flex;gap:8px;font-size:10.5px;line-height:12.5px;color:#888}
.perk svg{flex:none;margin-top:2px}
.perk-divider{top:60px;width:1px;height:40px;background:#ddd}

.hotline{left:663px;top:48px;font-size:13.5px;font-weight:700;color:#333;display:flex;align-items:center;gap:6px}
.mini-cart{left:808px;top:48px;font-size:11.5px;color:#666;display:flex;align-items:center;gap:6px}

.search{left:665px;top:81px;width:268px;height:38px;background:var(--lime);padding:7px 6px 6px 8px;display:flex;gap:6px}
.search .field{flex:1;background:#fff;border-radius:2px;font-size:11.5px;color:#555;padding:5px 6px}
.search .btn{width:56px;background:var(--red);color:#fff;font-weight:700;font-size:11.5px;border-radius:2px;text-align:center;line-height:25px}

.categories{left:115px;top:119px;width:168px;height:216px;background:#eee;border:1px solid #ddd;padding:4px 6px 0 6px}
.categories .head{height:27px;background:var(--red);color:#fff;font-size:13.5px;padding:4px 8px;display:flex;justify-content:space-between;align-items:center;border-radius:2px}
.categories ul{list-style:none;background:#fff}
.categories li{height:25.6px;border-bottom:1px solid #ddd;font-size:11.5px;padding:5px 6px;display:flex;justify-content:space-between;color:#444;white-space:nowrap}
.categories li span{color:#999}

.main-nav{left:283px;top:119px;width:650px;height:38px;background:linear-gradient(#fbfbfb,#ececec);border:1px solid #ddd;display:flex}
.main-nav a{padding:0 13px;line-height:37px;font-size:12.5px;color:#333;border-right:1px solid #d0d0d0;text-decoration:none}
.main-nav a.active{color:var(--red);width:61px;text-align:center;padding:0}

.side-box{left:115px;width:169px;background:var(--panel);border:1px solid #e4e4e4;border-radius:3px;padding:8px 7px}
.side-box h3{font-weight:400;font-size:13.5px;color:var(--red);padding-bottom:8px;border-bottom:3px double #ccc}
.side-box p{font-size:11.5px;line-height:15px;margin-top:10px;color:#444}

.support{left:115px;top:540px;width:169px;height:225px;background:linear-gradient(160deg,#1f4fae,#0b2a6d 60%,#1a4aa5);color:#fff;text-align:center;font-family:"Roboto Condensed",sans-serif;font-style:italic}
.support .t1{margin-top:28px;font-size:32px;font-weight:700;color:var(--yellow);line-height:32px;letter-spacing:-.5px}
.support .t2{font-size:22px;line-height:24px}
.support .t3{font-size:28px;font-weight:700;line-height:28px}
.support .t4{margin-top:22px;font-size:17px}
.support .phone{margin-top:2px;height:26px;background:var(--red);font-size:22px;font-style:normal;font-weight:700;line-height:26px}
.support .t5{margin-top:6px;font-size:15px;font-weight:700;color:var(--yellow)}

.poll label{display:flex;align-items:center;gap:6px;font-size:11.5px;margin-top:5px}
.poll .radio{width:11px;height:11px;border:1px solid #999;border-radius:50%;background:#fff}
.poll .vote{margin:8px 8px 0 auto;width:44px;height:23px;border:1px solid #ccc;background:linear-gradient(#fafafa,#e2e2e2);font-size:11.5px;text-align:center;line-height:21px;border-radius:2px}

.hero{left:291px;top:166px;width:642px;height:274px;background:linear-gradient(135deg,#fff,#eef0f3 60%,#e2e5ea);overflow:hidden}
.hero .title{position:absolute;top:30px;width:100%;text-align:center;font-family:"Roboto Condensed",sans-serif;font-style:italic}
.hero .title b{display:block;font-size:30px;color:var(--red);line-height:34px;letter-spacing:-.5px}
.hero .title i{display:block;font-size:20px;color:#222;line-height:24px}
.hero .title em{display:block;font-size:18px;color:var(--red);line-height:36px}
.hero .devices{position:absolute;left:62px;top:125px;width:520px;height:124px;background:linear-gradient(90deg,#c9cdd3,#3a4047 30%,#6a90a8 50%,#2f353c 75%,#c3c7cd);border-radius:8px;opacity:.85}
.hero .stripe{position:absolute;left:0;bottom:0;width:100%;height:14px;background:linear-gradient(100deg,var(--red) 66%,#c8c8c8 66.2%)}

.perk-tile{top:449px;width:159px;height:62px;text-align:center;font-family:"Roboto Condensed",sans-serif;font-size:16.5px;letter-spacing:.3px;border:1px solid #ddd}
.perk-tile svg{display:block;margin:4px auto 0}
.perk-tile.hot{background:linear-gradient(#ee6f58,var(--red-dark));color:#fff;border-color:var(--red-dark)}
.perk-tile.cool{background:linear-gradient(#fff,#ececec);color:var(--red)}

.product-panel{left:291px;width:642px;height:81px;background:var(--panel);border:1px solid #e4e4e4;border-radius:3px;padding:10px 9px}
.product-panel h3{font-weight:400;font-size:13.5px;color:var(--red);margin-left:4px}
.notice{margin-top:9px;height:34px;background:var(--notice);border:1px solid var(--notice-line);font-size:11.5px;color:#333;padding:8px 10px;display:flex;gap:6px;align-items:center}

.cat-tile{top:609px;width:207px;height:84px;border:1px solid #ddd;border-radius:3px;background:#fff;display:flex;align-items:center}
.cat-tile .pic{width:70px;height:72px;margin-left:8px;border-radius:4px}
.cat-tile .copy{flex:1;margin-left:12px;margin-right:8px;text-align:center;font-family:"Roboto Condensed",sans-serif}
.cat-tile .name{font-size:16px;color:#333;border-bottom:2px solid var(--red);padding-bottom:1px}
.cat-tile .link{font-family:"Open Sans",sans-serif;font-size:11.5px;color:var(--red);margin-top:1px}
</style>
</head>
<body>
<div class="viewport">
<div class="stage">

  <div class="abs top-bar"></div>
  <nav class="abs top-links">
    <span class="welcome">Default welcome msg!</span><span>My Account</span><span class="sep">|</span><span>My Wishlist</span><span class="sep">|</span><span>Checkout</span><span class="sep">|</span><span>Log In</span>
  </nav>

  <div class="abs brand"><span class="mark"></span>Lensport</div>

  <div class="abs perk" style="left:285px">
    <svg width="28" height="18" viewBox="0 0 28 18"><rect x="1" y="3" width="16" height="10" fill="#999"/><path d="M17 6h6l4 4v3H17z" fill="#aaa"/><circle cx="6" cy="14" r="3" fill="#777"/><circle cx="22" cy="14" r="3" fill="#777"/></svg>
    <span>Free Shipping<br>On All<br>Products</span>
  </div>
  <div class="abs perk-divider" style="left:401px"></div>
  <div class="abs perk" style="left:411px">
    <svg width="30" height="16" viewBox="0 0 30 16"><rect x="1" y="3" width="28" height="11" fill="#aaa"/><rect x="5" y="1" width="20" height="4" fill="#999"/></svg>
    <span>Money Back<br>Guarentee</span>
  </div>
  <div class="abs perk-divider" style="left:528px"></div>
  <div class="abs perk" style="left:538px">
    <svg width="18" height="20" viewBox="0 0 18 20"><rect x="1" y="7" width="16" height="12" fill="#aaa"/><rect x="0" y="5" width="18" height="4" fill="#888"/><rect x="8" y="5" width="2" height="14" fill="#fff"/></svg>
    <span>Special weekly<br>Offer</span>
  </div>

  <div class="abs hotline">
    <svg width="13" height="12" viewBox="0 0 13 12"><path d="M1 4c0-2 2-3 5.5-3S12 2 12 4h-3V3H4v1zM3 5h7l2 6H1z" fill="#444"/></svg>000 000 000
  </div>
  <div class="abs mini-cart">
    <svg width="24" height="18" viewBox="0 0 24 18"><path d="M0 1h4l3 10h12l3-8H6" fill="none" stroke="#7bb23a" stroke-width="2"/><circle cx="9" cy="15" r="2" fill="#7bb23a"/><circle cx="18" cy="15" r="2" fill="#7bb23a"/></svg>
    (0 item) - $0.00
    <svg width="10" height="6" viewBox="0 0 10 6"><path d="M0 0h10L5 6z" fill="#999"/></svg>
  </div>

  <div class="abs search"><div class="field">Search entire store here...</div><div class="btn">Search</div></div>

  <aside class="abs categories">
    <div class="head">Categories
      <svg width="16" height="16" viewBox="0 0 16 16"><circle cx="8" cy="8" r="8" fill="#fff"/><path d="M4.5 10l3.5-3.5 3.5 3.5" fill="none" stroke="var(--red)" stroke-width="2"/></svg>
    </div>
    <ul>
      <li>Analog Cameras<span>›</span></li>
      <li>Digital Video Recorders<span>›</span></li>
      <li>IP Cameras<span>›</span></li>
      <li>Network Video Recorders<span>›</span></li>
      <li>Accessories<span>›</span></li>
      <li>Network</li>
      <li style="border-bottom:0">Storage</li>
    </ul>
  </aside>

  <nav class="abs main-nav">
    <a class="active">Home</a><a>About Us</a><a>Privacy Policy</a><a>Customer Service</a>
  </nav>

  <section class="abs side-box" style="top:345px;height:88px"><h3>My Cart</h3><p>You have no items in your shopping cart.</p></section>
  <section class="abs side-box" style="top:445px;height:84px"><h3>Compare Products</h3><p>You have no items to compare.</p></section>

  <section class="abs support">
    <div class="t1">TECHNICAL</div>
    <div class="t2">support is</div>
    <div class="t3">Available</div>
    <div class="t4">Call us Now</div>
    <div class="phone">111-222-3333</div>
    <div class="t5">24 hours available</div>
  </section>

  <section class="abs side-box poll" style="top:775px;height:181px">
    <h3>Community Poll</h3>
    <p style="margin-top:10px;margin-bottom:4px;margin-left:3px">What is your favorite color</p>
    <label><span class="radio"></span>Green</label>
    <label><span class="radio"></span>Red</label>
    <label><span class="radio"></span>Black</label>
    <label><span class="radio"></span>Magenta</label>
    <div class="vote">Vote</div>
  </section>
  <section class="abs side-box" style="top:968px;height:41px;border-bottom:0;border-radius:3px 3px 0 0"><h3>Shop By Brand</h3></section>

  <section class="abs hero">
    <div class="title">
      <b>SMARTPHONE ACCESS</b>
      <i>View your cameras on any Fonix, Tabbo or Droidal phone or tablet</i>
      <em>CMS software for desktop Macra and Winset</em>
    </div>
    <div class="devices" role="img" aria-label="Row of smartphones showing live camera views"></div>
    <div class="stripe"></div>
  </section>

  <div class="abs perk-tile hot" style="left:291px">
    <svg width="26" height="26" viewBox="0 0 26 26"><path d="M14 2h9v9L11 23 2 14z" fill="#fff"/><circle cx="19" cy="6" r="2" fill="var(--red)"/></svg>LOWEST PRICES</div>
  <div class="abs perk-tile cool" style="left:452px">
    <svg width="26" height="26" viewBox="0 0 26 26"><rect x="6" y="4" width="12" height="10" fill="#e6c23a" transform="rotate(-20 12 9)"/><path d="M2 24L20 6M20 6l3-3" stroke="#333" stroke-width="2"/><circle cx="6" cy="22" r="3" fill="#333"/></svg>FREE SHIPPING</div>
  <div class="abs perk-tile hot" style="left:613px">
    <svg width="26" height="26" viewBox="0 0 26 26"><path d="M14 2h9v9L11 23 2 14z" fill="#fff"/><circle cx="19" cy="6" r="2" fill="var(--red)"/></svg>LOWEST PRICES</div>
  <div class="abs perk-tile cool" style="left:774px">
    <svg width="26" height="26" viewBox="0 0 26 26"><rect x="6" y="4" width="12" height="10" fill="#e6c23a" transform="rotate(-20 12 9)"/><path d="M2 24L20 6M20 6l3-3" stroke="#333" stroke-width="2"/><circle cx="6" cy="22" r="3" fill="#333"/></svg>FREE SHIPPING</div>

  <section class="abs product-panel" style="top:518px">
    <h3>Latest Products</h3>
    <div class="notice"><svg width="12" height="14" viewBox="0 0 12 14"><circle cx="6" cy="5" r="5" fill="#f2c230"/><rect x="4" y="10" width="4" height="3" fill="#999"/></svg>There are no products matching the selection.</div>
  </section>

  <div class="abs cat-tile" style="left:291px">
    <div class="pic" role="img" aria-label="Network video recorder unit" style="background:linear-gradient(#555,#1d1d1d)"></div>
    <div class="copy"><div class="name">Network Video</div><div class="link">See More</div></div>
  </div>
  <div class="abs cat-tile" style="left:508px">
    <div class="pic" role="img" aria-label="Pan tilt zoom dome camera" style="background:radial-gradient(circle,#f2f2f2,#bfc3c8)"></div>
    <div class="copy"><div class="name">Pan/Tilt/Zoom</div><div class="link">Shop Now</div></div>
  </div>
  <div class="abs cat-tile" style="left:726px">
    <div class="pic" role="img" aria-label="HD dome security camera" style="background:radial-gradient(circle,#fff,#c6c9cd);width:80px"></div>
    <div class="copy" style="margin-left:4px"><div class="name">1080P HD Video</div><div class="link">View All</div></div>
  </div>

  <section class="abs product-panel" style="top:706px">
    <h3>Featured Products</h3>
    <div class="notice"><svg width="12" height="14" viewBox="0 0 12 14"><circle cx="6" cy="5" r="5" fill="#f2c230"/><rect x="4" y="10" width="4" height="3" fill="#999"/></svg>There are no products matching the selection.</div>
  </section>

</div>
</div>
</body>
</html>
```